Business Card Design

we are a small based family business that specialise in 12v led lights for velmora caravans.
we also sell 12v switches, wire, circuit breakers, dimmers etc but our main line is LEDs.
We would like something that reflects the LED lighting on our cards.
www.ridgeglowleds.com.au is where you can have a look at to get ideas, of our product.
I have attached the logo we generally use on all our tradix listings and is the main header on our website.

Look forward to seeing what your team comes up with.

Industry/Entity Type

Business

Contact Information for Business Card

Tam 0438 207 915
Quorrin Vale QLD 4399

www.ridgeglowleds.com

```html
<!DOCTYPE html>
<html lang="en">
<head>
<meta charset="utf-8">
<title>Ridgeglow LEDs – Business Card</title>
<link href="https://fonts.googleapis.com/css2?family=Exo+2:wght@400;500;800&family=Oswald:wght@500&display=swap" rel="stylesheet">
<style>
  :root {
    --backdrop: #e9e6e1;
    --card-white: #ffffff;
    --brand-red: #b82a0c;
    --edge-black: #111111;
    --ink: #2b2b2b;
    --ink-soft: #555555;
  }
  html, body {
    margin: 0;
    width: 1200px;
    height: 987px;
    overflow: hidden;
    background: var(--backdrop);
  }
  .canvas {
    position: relative;
    width: 1200px;
    height: 987px;
    display: flex;
    justify-content: center;
    align-items: center;
    gap: 90px;
  }
  .card {
    position: relative;
    width: 380px;
    height: 660px;
    background: var(--card-white);
    box-shadow: 0 14px 30px rgba(0,0,0,.18);
    overflow: hidden;
  }
  .card-shapes {
    position: absolute;
    inset: 0;
    width: 380px;
    height: 660px;
  }
  .brand-name {
    position: absolute;
    left: 0;
    right: 0;
    text-align: center;
    font-family: "Exo 2", sans-serif;
    font-weight: 800;
    font-size: 30px;
    letter-spacing: 1px;
    line-height: 1;
    color: var(--edge-black);
    text-transform: uppercase;
  }
  .card-back .brand-name { top: 220px; }
  .card-front .brand-name { top: 110px; }

  .person {
    position: absolute;
    top: 215px;
    left: 0;
    right: 0;
    text-align: center;
  }
  .person-name {
    font-family: "Oswald", sans-serif;
    font-weight: 500;
    font-size: 30px;
    letter-spacing: 1px;
    color: var(--ink);
    text-transform: uppercase;
  }
  .person-role {
    font-family: "Exo 2", sans-serif;
    font-size: 15px;
    letter-spacing: 3px;
    color: var(--ink-soft);
    text-transform: uppercase;
    margin-top: 2px;
  }
  .contacts {
    position: absolute;
    top: 318px;
    left: 26px;
    right: 20px;
    display: grid;
    grid-template-columns: 1fr 1.45fr;
    row-gap: 14px;
    column-gap: 10px;
    font-family: "Exo 2", sans-serif;
    font-size: 12px;
    color: var(--ink);
  }
  .contact-item {
    display: flex;
    align-items: center;
    gap: 7px;
    white-space: nowrap;
  }
  .contact-icon {
    width: 16px;
    height: 16px;
    flex: none;
  }
  .address {
    position: absolute;
    top: 535px;
    left: 0;
    right: 0;
    text-align: center;
    font-family: "Exo 2", sans-serif;
    font-size: 14px;
    letter-spacing: 1px;
    line-height: 1.6;
    color: var(--card-white);
  }
  .address-pin {
    display: block;
    margin: 0 auto 8px;
    width: 30px;
    height: 30px;
  }
</style>
</head>
<body>
<main class="canvas">

  <!-- Reverse side -->
  <section class="card card-back" aria-label="Card reverse">
    <svg class="card-shapes" viewBox="0 0 380 660" aria-hidden="true">
      <polygon points="0,0 380,0 380,24 190,50 0,24" fill="var(--brand-red)"/>
      <polygon points="0,420 190,490 380,420 380,660 0,660" fill="var(--edge-black)"/>
      <polygon points="0,432 190,502 380,432 380,660 0,660" fill="var(--brand-red)"/>
    </svg>
    <div class="brand-name">Ridgeglow LEDs</div>
  </section>

  <!-- Front side -->
  <section class="card card-front" aria-label="Card front">
    <svg class="card-shapes" viewBox="0 0 380 660" aria-hidden="true">
      <polygon points="0,0 380,0 380,24 190,50 0,24" fill="var(--brand-red)"/>
      <polygon points="0,410 190,470 380,410 380,660 0,660" fill="var(--edge-black)"/>
      <polygon points="0,422 190,482 380,422 380,660 0,660" fill="var(--brand-red)"/>
    </svg>

    <div class="brand-name">Ridgeglow LEDs</div>

    <div class="person">
      <div class="person-name">Tam Corliss</div>
      <div class="person-role">General Manager</div>
    </div>

    <div class="contacts">
      <div class="contact-item">
        <svg class="contact-icon" viewBox="0 0 16 16" aria-hidden="true"><circle cx="8" cy="8" r="7" fill="none" stroke="var(--ink)" stroke-width="1.2"/><path d="M5.5 4.5l1.3 0 .6 1.8-.8.7a5 5 0 0 0 2.4 2.4l.7-.8 1.8.6 0 1.3c-3.5.2-6.2-2.5-6-6z" fill="var(--ink)"/></svg>
        <span>0438 207 915</span>
      </div>
      <div class="contact-item">
        <svg class="contact-icon" viewBox="0 0 16 16" aria-hidden="true"><circle cx="8" cy="8" r="7" fill="none" stroke="var(--ink)" stroke-width="1.2"/><rect x="4.3" y="5.3" width="7.4" height="5.4" fill="var(--ink)"/><path d="M4.3 5.3l3.7 3 3.7-3" fill="none" stroke="#fff" stroke-width=".8"/></svg>
        <span>tam@ridgeglowleds.com</span>
      </div>
      <div class="contact-item">
        <svg class="contact-icon" viewBox="0 0 16 16" aria-hidden="true"><circle cx="8" cy="8" r="7" fill="none" stroke="var(--ink)" stroke-width="1.2"/><path d="M5.5 4.5l1.3 0 .6 1.8-.8.7a5 5 0 0 0 2.4 2.4l.7-.8 1.8.6 0 1.3c-3.5.2-6.2-2.5-6-6z" fill="var(--ink)"/></svg>
        <span>0438 207 915</span>
      </div>
      <div class="contact-item">
        <svg class="contact-icon" viewBox="0 0 16 16" aria-hidden="true"><circle cx="8" cy="8" r="7" fill="none" stroke="var(--ink)" stroke-width="1.2"/><circle cx="8" cy="8" r="3.8" fill="none" stroke="var(--ink)" stroke-width="1"/><path d="M4.2 8h7.6M8 4.2v7.6" stroke="var(--ink)" stroke-width=".8"/></svg>
        <span>www.ridgeglowleds.com</span>
      </div>
    </div>

    <div class="address">
      <svg class="address-pin" viewBox="0 0 30 30" aria-hidden="true"><circle cx="15" cy="15" r="13.5" fill="none" stroke="var(--card-white)" stroke-width="1.6"/><path d="M15 7.5a5 5 0 0 0-5 5c0 3.6 5 9.5 5 9.5s5-5.9 5-9.5a5 5 0 0 0-5-5z" fill="var(--card-white)"/><circle cx="15" cy="12.5" r="1.9" fill="var(--brand-red)"/></svg>
      12 Kestrel Road<br>
      Quorrin Vale QLD 4399
    </div>
  </section>

</main>
</body>
</html>
```